Stationery Design Project for Nimbora, Chicago

Nimbora, a street parking application which helps car drivers find a street parking spot by offering an ideal path along which to look for parking. This path is calculated by our algorithm based on data (e.g. historical data, baseball games schedule, etc.). Along this path the driver will find a spot and will also save 70% of the search time. Customer we target is reg. between 21 and 45 yo.

We envision something young, fresh, bright and original. Slightly abstract maybe. It should represent the idea and elements of finding street parking in the city, e.g. car(s), parking spot, people, city, etc. (just ideas!).

Logo is attached.

Requirement:
- Business Cards (2 Sided Full Color CMYK)
- Letterhead (1 Sided Full Color CMYK)
- Envelope (1 Sided Full Color CMYK)
- Sticker (1 Sided Full Color CMYK), round with a 2inch diameter.

Reason: We're starting to get more and more designs and need more time to look into all of them. Very exciting!! Thanks to everybody!

Hi all, we're in the process of selecting our favs. Though choices!!! Really good submissions. Will keep you posted and sorry for the delay.

Target Market(s)

Car drivers and owners between 21 and 45

Industry/Entity Type

Parking

Requirements
Must have
• Sticker should be round and include company URL nimbora.com and the new logo which we will attach soon.
Should not have
• Should not be too serious or boring.

```html
<!DOCTYPE html>
<html lang="en">
<head>
<meta charset="utf-8">
<title>Nimbora Business Card</title>
<link href="https://fonts.googleapis.com/css2?family=Open+Sans:wght@400;600;700&display=swap" rel="stylesheet">
<style>
  :root {
    --page-bg: #d9d9d9;
    --card-white: #ffffff;
    --band-black: #0d0d0d;
    --band-mid: #2e2e2e;
    --rule-grey: #5a5a5a;
    --ink: #1a1a1a;
    --brand-blue: #1f4fc4;
    --asphalt-dark: #3f4144;
    --asphalt-mid: #6d6f72;
    --asphalt-light: #a4a6a8;
  }
  * { margin: 0; padding: 0; box-sizing: border-box; }
  html, body { width: 956px; height: 1200px; overflow: hidden; }
  body {
    background: var(--page-bg);
    font-family: "Open Sans", Arial, sans-serif;
    position: relative;
  }
  .card {
    position: absolute;
    left: 80px;
    width: 798px;
    height: 455px;
    border-radius: 28px;
    overflow: hidden;
    background: var(--card-white);
  }
  .card--front { top: 96px; }
  .card--back { top: 660px; background: var(--band-black); }

  .name-band {
    height: 76px;
    padding-top: 14px;
    background: radial-gradient(ellipse at 50% 40%, var(--band-mid), var(--band-black) 70%);
    color: #fff;
    display: flex;
    align-items: center;
    justify-content: center;
    gap: 6px;
  }
  .name-band .name { font-size: 23px; font-weight: 700; }
  .name-band .designation { font-size: 19px; font-weight: 600; }
  .rule { height: 7px; margin-top: 5px; background: var(--rule-grey); }

  .brand {
    display: flex;
    align-items: center;
    justify-content: center;
    gap: 28px;
  }
  .brand-dot {
    border-radius: 50%;
    background: var(--brand-blue);
    flex: none;
  }
  .brand-name { font-weight: 600; line-height: 1; }

  .card--front .brand { margin-top: 58px; padding-left: 24px; }
  .card--front .brand-dot { width: 148px; height: 148px; }
  .card--front .brand-name { font-size: 90px; color: var(--ink); }

  .contacts {
    margin-top: 38px;
    text-align: center;
    color: var(--ink);
    font-size: 20px;
    line-height: 33px;
  }
  .contacts b { font-weight: 700; }

  .photo-area {
    height: 297px;
    background:
      linear-gradient(150deg, var(--asphalt-dark) 0%, var(--asphalt-mid) 35%, var(--asphalt-light) 60%, var(--asphalt-mid) 85%, var(--asphalt-dark) 100%);
  }
  .back-band {
    height: 158px;
    background: radial-gradient(ellipse at 50% 40%, var(--band-mid), var(--band-black) 70%);
    display: flex;
    align-items: center;
    justify-content: center;
  }
  .back-band .brand { gap: 20px; padding-left: 24px; }
  .back-band .brand-dot { width: 104px; height: 104px; }
  .back-band .brand-name { font-size: 64px; color: #fff; }
</style>
</head>
<body>
  <section class="card card--front">
    <div class="name-band">
      <span class="name">Your Name -</span>
      <span class="designation">Designation</span>
    </div>
    <div class="rule"></div>
    <div class="brand">
      <span class="brand-dot"></span>
      <span class="brand-name">Nimbora</span>
    </div>
    <div class="contacts">
      <p><b>p</b> : 123-456-7890 &nbsp;|&nbsp; <b>c</b> : 123-456-7890</p>
      <p><b>e</b> : name@website.com &nbsp;|&nbsp; <b>w</b> : www.website.com</p>
      <p>City Name, Street Name, State Name, Country Code</p>
    </div>
  </section>

  <section class="card card--back">
    <div class="photo-area" role="img" aria-label="Photograph from above of cars parked in marked bays on grey asphalt beside a city street with a cyclist passing"></div>
    <div class="back-band">
      <div class="brand">
        <span class="brand-dot"></span>
        <span class="brand-name">Nimbora</span>
      </div>
    </div>
  </section>
</body>
</html>
```